UX - Need some screens design for a Skill Assessment Application

I am building an app to carry out skill assessments. Depending on how the assessment is configured, it may have one or more parts
1. Question based assessment (Multiple Choice, True False, Fill in the blanks"
2. Endorsement by two colleagues - A screen that allows user to pick colleagues based on search and shows the status of pending requests
3. A written submission - a page that explains the format of the submission and a file upload
As each assessment can be configured with or without any of the steps, the assessment UI must be such that these areas get hidden/displayed based on configuration.
Colour codes to be used can be #0e78bb and #ffffff
There will also be a start screen (instructions) and an end screen (results)
Target Market(s)
Enterprise software
Number of Pages Required
4 page

```html
<!DOCTYPE html>
<html lang="en">
<head>
<meta charset="utf-8">
<title>Skillora – Assessments Dashboard</title>
<link href="https://fonts.googleapis.com/css2?family=Inter:wght@400;500;600;700&display=swap" rel="stylesheet">
<style>
  :root {
    --brand-deep: #0457b0;
    --brand-card: #1a69be;
    --brand-icon: #3b7fc9;
    --brand: #0e78bb;
    --brand-bright: #1e8fd3;
    --line-light: rgba(255,255,255,.18);
    --white: #ffffff;
    --page: #f4f4f4;
    --text: #222a33;
    --muted: #555d66;
    --chip: #e8e9ea;
    --tick: #129c9f;
    --menu: #666666;
    --photo: #8a6e66;
  }
  * { box-sizing: border-box; margin: 0; padding: 0; }
  html, body { width: 1200px; height: 771px; overflow: hidden; }
  body { font-family: 'Inter', sans-serif; background: var(--page); color: var(--text); }

  .hero { background: var(--brand-deep); height: 288px; color: var(--white); }
  .topbar { height: 43px; border-bottom: 1px solid var(--line-light); position: relative; display: flex; align-items: center; padding: 0 70px; }
  .brand { display: flex; align-items: center; gap: 8px; font-size: 14px; font-weight: 600; }
  .brand-mark { width: 18px; height: 18px; border-radius: 50%; background: var(--white); }
  .nav { position: absolute; left: 488px; top: 0; display: flex; gap: 21px; height: 43px; }
  .nav a { color: rgba(255,255,255,.85); text-decoration: none; font-size: 12.5px; line-height: 43px; position: relative; }
  .nav a.active { color: var(--white); font-weight: 600; }
  .nav a.active::after { content: ""; position: absolute; left: 0; right: 0; bottom: 0; height: 3px; background: var(--brand-bright); }
  .top-actions { position: absolute; right: 70px; top: 8px; display: flex; align-items: center; gap: 17px; }
  .avatar { border-radius: 50%; background: linear-gradient(135deg, #3a2e2f, var(--photo)); }
  .avatar.sm { width: 27px; height: 27px; }
  .avatar.lg { width: 43px; height: 43px; }

  .welcome { display: flex; align-items: center; gap: 21px; padding: 28px 57px 0; position: relative; }
  .welcome small { display: block; font-size: 12px; color: #8fc2f0; margin-bottom: 5px; }
  .welcome strong { font-size: 17px; font-weight: 600; }
  .btn-create { position: absolute; right: 58px; top: 32px; width: 177px; height: 34px; background: var(--brand-bright); color: var(--white); border-radius: 3px; display: flex; align-items: center; justify-content: center; gap: 7px; font-size: 11.5px; font-weight: 500; }

  .summary-title { font-size: 13.5px; font-weight: 500; padding: 24px 57px 12px; }
  .summary { display: grid; grid-template-columns: repeat(4, 260px); gap: 15px; padding: 0 57px; }
  .stat { background: var(--brand-card); height: 89px; border-radius: 3px; display: flex; padding: 14px; gap: 17px; }
  .stat-icon { width: 34px; height: 34px; background: var(--brand-icon); border-radius: 2px; display: flex; align-items: center; justify-content: center; flex: none; }
  .stat-num { font-size: 17px; font-weight: 600; margin-top: 9px; }
  .stat-label { font-size: 12.5px; margin-top: 4px; }
  .stat-sub { font-size: 9.5px; color: #c9def3; margin-top: 3px; }

  .section { padding: 20px 71px 0; position: relative; }
  .section h2 { font-size: 17px; font-weight: 600; }
  .tabs { display: flex; margin-top: 18px; height: 31px; }
  .tab { font-size: 11.5px; display: flex; align-items: center; justify-content: center; border-radius: 3px 0 0 3px; background: #e4e5e6; color: var(--muted); width: 88px; }
  .tab b { font-weight: 600; margin-left: 4px; }
  .tab.active { background: var(--brand); color: var(--white); border-radius: 0 3px 3px 0; width: 103px; }
  .views { position: absolute; right: 71px; top: 73px; display: flex; gap: 17px; }

  .grid { display: grid; grid-template-columns: repeat(3, 340px); gap: 19px 19px; margin-top: 20px; }
  .card { background: var(--white); height: 167px; border-radius: 3px; padding: 20px 21px; position: relative; }
  .card-id { font-size: 12.5px; color: var(--muted); }
  .card-title { font-size: 12.5px; color: var(--brand); margin-top: 9px; }
  .dates { display: flex; margin-top: 14px; }
  .dates div { width: 125px; }
  .dates span { display: block; font-size: 9.5px; color: var(--muted); }
  .dates time { display: block; font-size: 12.5px; color: var(--muted); margin-top: 6px; }
  .kebab { position: absolute; right: 21px; top: 20px; }
  .chips { display: flex; gap: 7px; margin-top: 17px; }
  .chip { height: 22px; border-radius: 11px; background: var(--chip); font-size: 11.5px; color: var(--muted); display: flex; align-items: center; gap: 6px; padding: 0 6px 0 9px; }
  .menu { position: absolute; left: 221px; top: 7px; width: 89px; height: 86px; background: var(--menu); border-radius: 3px; color: var(--white); font-size: 11.5px; text-align: right; padding: 12px 12px; line-height: 22px; }
</style>
</head>
<body>
  <header class="hero">
    <div class="topbar">
      <div class="brand"><span class="brand-mark"></span>Skillora</div>
      <nav class="nav">
        <a class="active" href="#">Assessments</a>
        <a href="#">Colleagues</a>
        <a href="#">Results</a>
      </nav>
      <div class="top-actions">
        <svg width="18" height="18" viewBox="0 0 24 24" fill="none" stroke="#fff" stroke-width="1.6"><path d="M6 16V11a6 6 0 0112 0v5l2 2H4z"/><path d="M10 20a2 2 0 004 0"/></svg>
        <svg width="18" height="18" viewBox="0 0 24 24" fill="none" stroke="#fff" stroke-width="1.6"><circle cx="12" cy="12" r="3"/><path d="M12 2l2 3 3.5-.5.5 3.5 3 2-2 3 .5 3.5-3.5.5-2 3-2-3-3.5.5-.5-3.5-3-2 2-3-.5-3.5 3.5-.5z"/></svg>
        <div class="avatar sm" role="img" aria-label="User profile photo"></div>
      </div>
    </div>

    <div class="welcome">
      <div class="avatar lg" role="img" aria-label="User profile photo"></div>
      <div><small>Welcome back!</small><strong>Maya L. Hartono</strong></div>
      <div class="btn-create">
        <svg width="13" height="13" viewBox="0 0 24 24" fill="none" stroke="#fff" stroke-width="2"><path d="M5 3h11v8M5 3v18h8"/><circle cx="17" cy="17" r="3"/><path d="M19 19l2 2"/></svg>
        Create New Assessment
      </div>
    </div>

    <h3 class="summary-title">Summary</h3>
    <div class="summary">
      <div class="stat">
        <div class="stat-icon"><svg width="20" height="20" viewBox="0 0 24 24" fill="none" stroke="#fff" stroke-width="1.6"><path d="M5 3h12v9M5 3v18h8M8 8h6M8 12h4"/><circle cx="17" cy="17" r="3"/><path d="M16 17l1 1 2-2"/></svg></div>
        <div><div class="stat-num">7</div><div class="stat-label">My Assessments</div><div class="stat-sub">3 pending</div></div>
      </div>
      <div class="stat">
        <div class="stat-icon"><svg width="20" height="20" viewBox="0 0 24 24" fill="none" stroke="#fff" stroke-width="1.6"><path d="M12 3l1.5 3 3 .4-2.2 2 .6 3-2.9-1.6L9.1 11.4l.6-3-2.2-2 3-.4z"/><path d="M3 14h3v7H3zM6 15h5l3 2h3a2 2 0 010 3H6"/></svg></div>
        <div><div class="stat-num">3</div><div class="stat-label">Endorsements</div><div class="stat-sub">1 pending</div></div>
      </div>
      <div class="stat">
        <div class="stat-icon"><svg width="20" height="20" viewBox="0 0 24 24" fill="none" stroke="#fff" stroke-width="1.6"><circle cx="7" cy="6" r="2.5"/><circle cx="17" cy="6" r="2.5"/><circle cx="12" cy="12" r="2.5"/><path d="M2 14a5 5 0 019 0M13 14a5 5 0 019 0M7 21a5 5 0 0110 0"/></svg></div>
        <div><div class="stat-num">10</div><div class="stat-label">Colleagues</div><div class="stat-sub">Last updated on May 23, 2024</div></div>
      </div>
      <div class="stat">
        <div class="stat-icon"><svg width="20" height="20" viewBox="0 0 24 24" fill="none" stroke="#fff" stroke-width="1.6"><path d="M12 15V3M8 7l4-4 4 4"/><path d="M3 13v7h18v-7M3 13h5l1 3h6l1-3h5"/></svg></div>
        <div><div class="stat-num">7</div><div class="stat-label">Submissions</div><div class="stat-sub">Last submit on May 23, 2024</div></div>
      </div>
    </div>
  </header>

  <main class="section">
    <h2>Assessments</h2>
    <div class="tabs">
      <div class="tab">Pending<b>2</b></div>
      <div class="tab active">Completed<b>5</b></div>
    </div>
    <div class="views">
      <svg width="19" height="17" viewBox="0 0 20 18" fill="none" stroke="#0e78bb" stroke-width="1.6"><path d="M1 2h2M6 2h13M1 9h2M6 9h13M1 16h2M6 16h13"/></svg>
      <svg width="18" height="18" viewBox="0 0 18 18" fill="none" stroke="#8a8f95" stroke-width="1.4"><rect x="1" y="1" width="6" height="6"/><rect x="11" y="1" width="6" height="6"/><rect x="1" y="11" width="6" height="6"/><rect x="11" y="11" width="6" height="6"/></svg>
    </div>

    <div class="grid">
      <article class="card">
        <div class="card-id">1723091983</div>
        <div class="card-title">UI/UX Designer Assessments</div>
        <div class="dates"><div><span>PUBLISHED ON</span><time>20/05/2024</time></div><div><span>DUE DATE</span><time>24/05/2024</time></div></div>
        <div class="chips">
          <span class="chip">Quiz <svg width="13" height="13" viewBox="0 0 14 14"><circle cx="7" cy="7" r="7" fill="#129c9f"/><path d="M4 7l2 2 4-4" stroke="#fff" stroke-width="1.5" fill="none"/></svg></span>
          <span class="chip">Endorsement <svg width="13" height="13" viewBox="0 0 14 14"><circle cx="7" cy="7" r="7" fill="#129c9f"/><path d="M4 7l2 2 4-4" stroke="#fff" stroke-width="1.5" fill="none"/></svg></span>
        </div>
        <div class="menu">Edit<br>Delete<br>Review</div>
        <svg class="kebab" width="4" height="16" viewBox="0 0 4 16" fill="#1e8fd3"><circle cx="2" cy="2" r="1.7"/><circle cx="2" cy="8" r="1.7"/><circle cx="2" cy="14" r="1.7"/></svg>
      </article>

      <article class="card">
        <div class="card-id">1723091983</div>
        <div class="card-title">Front-end Developer Assessments</div>
        <div class="dates"><div><span>PUBLISHED ON</span><time>20/05/2024</time></div><div><span>DUE DATE</span><time>24/05/2024</time></div></div>
        <div class="chips">
          <span class="chip">Endorsement <svg width="13" height="13" viewBox="0 0 14 14"><circle cx="7" cy="7" r="7" fill="#129c9f"/><path d="M4 7l2 2 4-4" stroke="#fff" stroke-width="1.5" fill="none"/></svg></span>
          <span class="chip">Submission <svg width="13" height="13" viewBox="0 0 14 14"><circle cx="7" cy="7" r="7" fill="#129c9f"/><path d="M4 7l2 2 4-4" stroke="#fff" stroke-width="1.5" fill="none"/></svg></span>
        </div>
        <svg class="kebab" width="4" height="16" viewBox="0 0 4 16" fill="#555d66"><circle cx="2" cy="2" r="1.7"/><circle cx="2" cy="8" r="1.7"/><circle cx="2" cy="14" r="1.7"/></svg>
      </article>

      <article class="card">
        <div class="card-id">1723091983</div>
        <div class="card-title">Cybersecurity Analyst Assessments</div>
        <div class="dates"><div><span>PUBLISHED ON</span><time>20/05/2024</time></div><div><span>DUE DATE</span><time>24/05/2024</time></div></div>
        <div class="chips">
          <span class="chip">Quiz <svg width="13" height="13" viewBox="0 0 14 14"><circle cx="7" cy="7" r="7" fill="#129c9f"/><path d="M4 7l2 2 4-4" stroke="#fff" stroke-width="1.5" fill="none"/></svg></span>
        </div>
        <svg class="kebab" width="4" height="16" viewBox="0 0 4 16" fill="#555d66"><circle cx="2" cy="2" r="1.7"/><circle cx="2" cy="8" r="1.7"/><circle cx="2" cy="14" r="1.7"/></svg>
      </article>

      <article class="card">
        <div class="card-id">1723091983</div>
        <div class="card-title">DevOps Engineer Assessments</div>
        <div class="dates"><div><span>PUBLISHED ON</span><time>20/05/2024</time></div><div><span>DUE DATE</span><time>24/05/2024</time></div></div>
        <div class="chips">
          <span class="chip">Quiz <svg width="13" height="13" viewBox="0 0 14 14"><circle cx="7" cy="7" r="7" fill="#129c9f"/><path d="M4 7l2 2 4-4" stroke="#fff" stroke-width="1.5" fill="none"/></svg></span>
          <span class="chip">Endorsement <svg width="13" height="13" viewBox="0 0 14 14"><circle cx="7" cy="7" r="7" fill="#129c9f"/><path d="M4 7l2 2 4-4" stroke="#fff" stroke-width="1.5" fill="none"/></svg></span>
          <span class="chip">Submission <svg width="13" height="13" viewBox="0 0 14 14"><circle cx="7" cy="7" r="7" fill="#129c9f"/><path d="M4 7l2 2 4-4" stroke="#fff" stroke-width="1.5" fill="none"/></svg></span>
        </div>
        <svg class="kebab" width="4" height="16" viewBox="0 0 4 16" fill="#555d66"><circle cx="2" cy="2" r="1.7"/><circle cx="2" cy="8" r="1.7"/><circle cx="2" cy="14" r="1.7"/></svg>
      </article>

      <article class="card">
        <div class="card-id">1723091983</div>
        <div class="card-title">Sales Representative Assessments</div>
        <div class="dates"><div><span>PUBLISHED ON</span><time>20/05/2024</time></div><div><span>DUE DATE</span><time>24/05/2024</time></div></div>
        <div class="chips">
          <span class="chip">Quiz <svg width="13" height="13" viewBox="0 0 14 14"><circle cx="7" cy="7" r="7" fill="#129c9f"/><path d="M4 7l2 2 4-4" stroke="#fff" stroke-width="1.5" fill="none"/></svg></span>
          <span class="chip">Endorsement <svg width="13" height="13" viewBox="0 0 14 14"><circle cx="7" cy="7" r="7" fill="#129c9f"/><path d="M4 7l2 2 4-4" stroke="#fff" stroke-width="1.5" fill="none"/></svg></span>
        </div>
        <svg class="kebab" width="4" height="16" viewBox="0 0 4 16" fill="#555d66"><circle cx="2" cy="2" r="1.7"/><circle cx="2" cy="8" r="1.7"/><circle cx="2" cy="14" r="1.7"/></svg>
      </article>
    </div>
  </main>
</body>
</html>
```